Tech business card design

We need an amazing business card design for our new business 'Pexla' a marketing tech startup based in Sydney, Australia. We provide an online marketplace for businesses to search and buy advertising media, connect with service providers and learn more about marketing. We wish to communicate 'cool tech', reliability and professionalism and design based around our logo.

Target Market(s)

Business Owners

Contact Information for Business Card

Name
Position
Email Address
Website
Phone Number

Font styles to use
Other font styles liked:
• Avenir & Avenir Next

Colors

Designer to choose colors to be used in the design.

```html
<!DOCTYPE html>
<html lang="en">
<head>
<meta charset="utf-8">
<title>Pexla Business Card</title>
<link href="https://fonts.googleapis.com/css2?family=Nunito+Sans:wght@400;600;800;900&display=swap" rel="stylesheet">
<style>
  :root {
    --backdrop: #ececec;
    --navy: #28244f;
    --paper: #ffffff;
    --ink: #1f1c3f;
  }
  * { box-sizing: border-box; margin: 0; padding: 0; }
  html, body {
    width: 1200px;
    height: 800px;
    overflow: hidden;
    background: var(--backdrop);
    font-family: "Nunito Sans", sans-serif;
  }
  .canvas {
    position: relative;
    width: 1200px;
    height: 800px;
  }
  .card {
    position: absolute;
    top: 278px;
    width: 420px;
    height: 240px;
  }
  .card--front {
    left: 142px;
    background: var(--navy);
    display: flex;
    align-items: center;
    justify-content: center;
  }
  .card--back {
    left: 638px;
    background: var(--paper);
    color: var(--ink);
  }
  .wordmark {
    font-family: "Nunito Sans", sans-serif;
    font-weight: 900;
    letter-spacing: -1px;
    line-height: 1;
  }
  .card--front .wordmark {
    color: var(--paper);
    font-size: 76px;
    margin-top: -6px;
  }
  .card--back .wordmark {
    position: absolute;
    left: 34px;
    top: 38px;
    color: var(--ink);
    font-size: 60px;
  }
  .person {
    position: absolute;
    left: 40px;
    top: 144px;
  }
  .person__name {
    font-size: 18px;
    font-weight: 800;
    letter-spacing: 0.6px;
    text-transform: uppercase;
    line-height: 1.15;
  }
  .person__role {
    font-size: 14px;
    font-weight: 400;
    line-height: 1.2;
    margin-left: 1px;
  }
  .contact {
    position: absolute;
    left: 224px;
    top: 144px;
    list-style: none;
  }
  .contact__item {
    display: flex;
    align-items: center;
    gap: 9px;
    font-size: 15px;
    line-height: 20px;
  }
  .contact__icon {
    width: 11px;
    height: 11px;
    flex: none;
  }
</style>
</head>
<body>
<main class="canvas">
  <section class="card card--front" aria-label="Card front">
    <span class="wordmark">pexla</span>
  </section>

  <section class="card card--back" aria-label="Card back">
    <span class="wordmark">pexla</span>

    <div class="person">
      <p class="person__name">Liam Carter</p>
      <p class="person__role">General Manager</p>
    </div>

    <ul class="contact">
      <li class="contact__item">
        <svg class="contact__icon" viewBox="0 0 12 12" aria-hidden="true">
          <circle cx="6" cy="6" r="6" fill="var(--ink)"/>
          <path d="M4 3.2c.3-.2.6-.1.8.2l.5.9c.1.3 0 .5-.2.7l-.3.3c.3.7.9 1.3 1.6 1.6l.3-.3c.2-.2.5-.3.7-.2l.9.5c.3.2.4.5.2.8l-.4.5c-.3.3-.8.4-1.2.2C5.3 7.8 4.2 6.7 3.6 5.1c-.2-.4-.1-.9.2-1.2z" fill="var(--paper)"/>
        </svg>
        <span>012 345 6789</span>
      </li>
      <li class="contact__item">
        <svg class="contact__icon" viewBox="0 0 12 12" aria-hidden="true">
          <rect x="0.5" y="2.5" width="11" height="7.5" rx="1" fill="var(--ink)"/>
          <path d="M1 3.2 6 6.6l5-3.4" fill="none" stroke="var(--paper)" stroke-width="1"/>
        </svg>
        <span>your@email.com</span>
      </li>
      <li class="contact__item">
        <svg class="contact__icon" viewBox="0 0 12 12" aria-hidden="true">
          <circle cx="6" cy="6" r="5.5" fill="var(--ink)"/>
          <g fill="none" stroke="var(--paper)" stroke-width="0.8">
            <ellipse cx="6" cy="6" rx="2.3" ry="5.3"/>
            <path d="M0.8 6h10.4M1.6 3.4h8.8M1.6 8.6h8.8"/>
          </g>
        </svg>
        <span>www.website.com</span>
      </li>
    </ul>
  </section>
</main>
</body>
</html>
```